Business Card - high end, modern health care

Hey designers!

We need a double sided business card for the boutique, cutting edge physical therapy rehabilitation centre in Sydney's Northern Beaches.

With the most qualified physios in the area The Harbourview Motion Clinic does what other physiotherapy practices do not, we take our time with our patients giving them longer appointments, better physios and therefor faster results!

We guarantee that the service people receive at THMC will be unparalleled.

Hence we need a business card to reflect our modern, boutique, high end service. The final design needs to reflect that we are in a class of our own yet with the feel of beachside retreat.

Below I have attached our logo in both blue on white and white on blue. The exact colour is;
and the font that we have used in our logo is Tex Gyre Aventador.

I like the idea of the blue as the main colour as it is more eye catching and our signage onto the main road will be in this blue and in the interest of consistency across marketing the blue needs to be a part of the design. However I would appreciate a few designs onto a wooden background as this is a visual theme within the fitout of the practice.

The design needs to be of standard size (91x55mm).

Target Market(s)

We target people who have an end outcome in mind and those who have had poor experiences with other providers and ensure that everyone gets the care that they deserve with a premium service that is tailored to the individuals circumstances. As a premium service, the target market is highly educated, business and tech savvy with the additional target market of elderly people who have self funded their retirement and see value in paying for the best ongoing rehabilitation to maintain independence.

Industry/Entity Type

Physical Therapy

Contact Information for Business Card

Name, designation( Titled Musculoskeletal Physiotherapist... there will also be those in the company that have multiple designations ie 5 or 6 words long), phone number, email, facebook, instagram, address

Font styles to use
Sans Serif

Colors

Designer to choose colors to be used in the design.

Requirements
Must have
• Front - The logo as large as possible, blue or wooden theme, and all of the important details.
• Back - A blank space/lines on which to write appointment times (no "Appointment, date, time" etc.)
Nice to have
• facebook url
• logos for facebook and instagram
• Mini logos for the phone and email?

```html
<!DOCTYPE html>
<html lang="en">
<head>
<meta charset="utf-8">
<title>The Harbourview Motion Clinic – Business Card</title>
<link href="https://fonts.googleapis.com/css2?family=Roboto:wght@300;400;500&family=Montserrat:wght@600;700&display=swap" rel="stylesheet">
<style>
  :root {
    --brand-blue: #0a55ae;
    --ink: #4a4a4a;
    --ink-soft: #6c6c6c;
    --rule: #c9c9c9;
    --grey-band: #55585c;
    --card: #fbfbfb;
    --stage: #ecebe8;
  }
  * { box-sizing: border-box; margin: 0; padding: 0; }
  html, body { width: 1200px; height: 911px; overflow: hidden; }
  body {
    background: var(--stage);
    font-family: "Roboto", Arial, sans-serif;
    position: relative;
  }
  .card {
    position: absolute;
    width: 546px;
    height: 330px;
    background: var(--card);
    border-radius: 18px;
    box-shadow: 0 6px 18px rgba(0,0,0,.18);
    overflow: hidden;
  }
  .card--front { left: 40px; top: 120px; }
  .card--back { left: 614px; top: 460px; }

  /* Front */
  .brand {
    position: absolute; left: 34px; top: 58px; width: 210px;
    display: flex; flex-direction: column; align-items: center; gap: 14px;
    color: var(--brand-blue);
  }
  .brand__dot {
    width: 118px; height: 118px; border-radius: 50%;
    background: var(--brand-blue);
  }
  .brand__name {
    font-family: "Montserrat", Arial, sans-serif; font-weight: 700;
    font-size: 19px; line-height: 1.15; text-align: center;
    text-transform: uppercase; letter-spacing: .02em;
  }
  .divider {
    position: absolute; left: 262px; top: 40px; width: 1px; height: 170px;
    background: var(--rule);
  }
  .details { position: absolute; left: 290px; top: 46px; right: 20px; color: var(--ink); }
  .details__name {
    font-family: "Montserrat", Arial, sans-serif; font-weight: 700;
    font-size: 22px; color: var(--brand-blue); text-transform: uppercase;
  }
  .details__title { font-size: 13px; color: var(--ink); margin-top: 2px; text-transform: uppercase; }
  .details__address { font-size: 12px; font-weight: 300; line-height: 1.4; margin-top: 18px; }
  .contact-list { list-style: none; margin-top: 10px; font-size: 12px; font-weight: 300; }
  .contact-list li { display: flex; align-items: center; gap: 8px; line-height: 1.5; }
  .contact-list svg { width: 11px; height: 11px; fill: var(--brand-blue); flex: none; }
  .band {
    position: absolute; left: 0; right: 0; bottom: 22px; height: 36px;
    display: flex; align-items: center;
  }
  .band__blue {
    flex: 1; height: 100%; background: var(--brand-blue);
    display: flex; align-items: center; padding-left: 230px;
    color: #fff; font-size: 14px; letter-spacing: .18em;
  }
  .band__dot {
    width: 40px; height: 40px; border-radius: 50%;
    background: #fff; border: 4px solid var(--brand-blue); flex: none;
    margin: 0 -2px;
  }
  .band__grey { width: 74px; height: 100%; background: var(--grey-band); }

  /* Back */
  .appointments { position: absolute; left: 38px; right: 38px; top: 34px; }
  .appt-row {
    display: flex; align-items: flex-end; gap: 6px;
    font-size: 14px; color: var(--ink-soft); height: 30px;
  }
  .appt-row .fill { flex: 1; border-bottom: 1px solid #8a8a8a; height: 100%; }
  .appt-row .fill--short { flex: 0 0 110px; }
  .write-line { height: 30px; border-bottom: 1px solid #8a8a8a; }
</style>
</head>
<body>

<article class="card card--front" aria-label="Business card front">
  <div class="brand">
    <span class="brand__dot" aria-hidden="true"></span>
    <span class="brand__name">The Harbourview<br>Motion Clinic</span>
  </div>
  <span class="divider" aria-hidden="true"></span>
  <div class="details">
    <h1 class="details__name">Liam Carver</h1>
    <p class="details__title">CEO/Founder</p>
    <p class="details__address">42 Seabreeze Parade<br>Harbour Point, NSW 2099</p>
    <ul class="contact-list">
      <li><svg viewBox="0 0 24 24"><path d="M6.6 10.8a15 15 0 0 0 6.6 6.6l2.2-2.2c.3-.3.7-.4 1-.2 1.1.4 2.3.6 3.6.6.6 0 1 .4 1 1V20c0 .6-.4 1-1 1A17 17 0 0 1 3 4c0-.6.4-1 1-1h3.5c.6 0 1 .4 1 1 0 1.2.2 2.4.6 3.6.1.3 0 .7-.2 1z"/></svg>555 018 2746</li>
      <li><svg viewBox="0 0 24 24"><path d="M2 5h20v14H2zm2 2v.5l8 5 8-5V7l-8 5z"/></svg>liam@harbourview.example</li>
      <li><svg viewBox="0 0 24 24"><rect x="2" y="2" width="20" height="20" rx="3"/></svg>/harbourviewmotion</li>
      <li><svg viewBox="0 0 24 24"><rect x="2" y="2" width="20" height="20" rx="3"/></svg>@harbourviewclinic</li>
    </ul>
  </div>
  <div class="band">
    <div class="band__blue">www.harbourview.example</div>
    <span class="band__dot" aria-hidden="true"></span>
    <div class="band__grey"></div>
  </div>
</article>

<article class="card card--back" aria-label="Business card back, appointment lines">
  <div class="appointments">
    <div class="appt-row"><span>Date</span><span class="fill"></span><span>Time</span><span class="fill fill--short"></span><span>am/pm</span></div>
    <div class="appt-row"><span>Date</span><span class="fill"></span><span>Time</span><span class="fill fill--short"></span><span>am/pm</span></div>
    <div class="write-line"></div>
    <div class="write-line"></div>
    <div class="write-line"></div>
    <div class="write-line"></div>
    <div class="write-line"></div>
    <div class="write-line"></div>
  </div>
</article>

</body>
</html>
```